Website design for company that sells taximeters and has a taxi dispatch call center, webstore neede

Need a website with a shop with at least 20 articles, in two languages, possibly by using a purchased theme (not purchased yet).The company provides equipments and dispatch solutions for taxi companies. Typical yellow and black theme

Target Market(s)

Taxi companies

Industry/Entity Type

Taxi

Number of Pages Required

3 page

Font styles to use
Sans Serif

Colors
fbed22
000000

Requirements
Must have
• - webstore for at least 20 articles
• - Documents folder where to put pdf material related to taximeters
• - contact form message submission
Nice to have
• Feedback section
Should not have
• Blogs,

```html
<!DOCTYPE html>
<html lang="en">
<head>
<meta charset="utf-8">
<title>Fareline – Radio Networks</title>
<link rel="stylesheet" href="https://fonts.googleapis.com/css2?family=Open+Sans:wght@400;600;700;800&family=Varela+Round&display=swap">
<style>
  :root {
    --yellow: #fbd22a;
    --black: #000000;
    --footer: #0b0b0b;
    --ink: #2e2e2e;
    --body-grey: #6b6b6b;
    --white: #ffffff;
    --rule: #555555;
  }
  * { margin: 0; padding: 0; box-sizing: border-box; }
  html, body { width: 850px; height: 1200px; overflow: hidden; background: var(--white); }
  body { position: relative; font-family: "Open Sans", Arial, sans-serif; color: var(--ink); }

  .hero {
    position: absolute; left: 0; top: 0; width: 850px; height: 203px;
    background:
      radial-gradient(ellipse at 70% 40%, rgba(190,70,30,.55), transparent 55%),
      linear-gradient(160deg, #2b2d30 0%, #1a1b1e 40%, #3a2a22 70%, #14171a 100%);
  }
  .site-header { position: absolute; left: 0; top: 0; width: 850px; height: 40px; }
  .brand {
    position: absolute; left: 106px; top: 9px;
    font-family: "Open Sans", sans-serif; font-weight: 800; font-size: 17px;
    letter-spacing: 1px; color: var(--yellow);
  }
  .main-nav { position: absolute; left: 271px; top: 15px; display: flex; gap: 6px; }
  .main-nav a {
    font-size: 7px; font-weight: 700; letter-spacing: .5px; color: var(--white);
    text-decoration: none;
  }
  .main-nav a.active { color: var(--yellow); }
  .phone { position: absolute; left: 534px; top: 11px; display: flex; align-items: center; gap: 8px; }
  .phone-number { font-size: 8px; font-weight: 700; letter-spacing: 1.2px; color: var(--yellow); }
  .lang { font-size: 7px; font-weight: 700; color: var(--white); letter-spacing: .5px; }
  .search {
    position: absolute; left: 696px; top: 10px; width: 108px; height: 20px;
    border: 1.5px solid var(--yellow); border-radius: 10px;
    font-size: 9px; letter-spacing: 1px; color: #d8d8d8; padding: 3px 0 0 11px;
  }
  .search svg { position: absolute; right: 9px; top: 4px; }
  .hero-title {
    position: absolute; left: 0; top: 80px; width: 874px; text-align: center;
    font-family: "Varela Round", sans-serif; font-size: 21px; letter-spacing: 2px; color: var(--white);
  }
  .hero-tagline {
    position: absolute; left: 0; top: 114px; width: 874px; text-align: center;
    font-size: 8px; font-weight: 700; letter-spacing: 1px; color: var(--white);
  }

  .intro-title {
    position: absolute; left: 0; top: 250px; width: 874px; text-align: center;
    font-size: 22px; font-weight: 600; letter-spacing: -1px; color: #333;
  }
  .intro-rule { position: absolute; left: 403px; top: 294px; width: 56px; height: 3px; background: var(--yellow); }

  .topic { position: absolute; left: 177px; width: 520px; }
  .topic h2 { font-size: 18px; font-weight: 700; letter-spacing: 2px; color: #2a2a2a; line-height: 22px; margin-bottom: 1px; }
  .topic p { font-size: 13.2px; line-height: 16.2px; color: var(--body-grey); margin-bottom: 16px; }
  .topic-uhf { top: 333px; }
  .topic-capability { top: 539px; }
  .topic-coverage { top: 745px; }

  .site-footer { position: absolute; left: 0; top: 1032px; width: 850px; height: 168px; background: var(--footer); color: var(--white); }
  .footer-col { position: absolute; top: 30px; width: 125px; }
  .footer-col h3 { font-size: 6.5px; font-weight: 700; margin-bottom: 9px; }
  .footer-col h3 span, .footer-col a { color: var(--yellow); text-decoration: none; }
  .footer-col p { font-size: 6px; line-height: 10.5px; }
  .col-about { left: 179px; } .col-contact { left: 307px; } .col-hours { left: 435px; } .col-links { left: 562px; }
  .social { display: flex; gap: 4px; margin-top: 1px; }
  .social span { width: 9px; height: 9px; border-radius: 50%; background: var(--white); display: block; }
  .footer-rule { position: absolute; left: 179px; top: 101px; width: 500px; height: 1px; background: var(--rule); }
  .legal { position: absolute; left: 179px; top: 110px; font-size: 5.5px; }
  .legal a { color: var(--yellow); text-decoration: none; }
  .legal .sep { margin-left: 16px; }
</style>
</head>
<body>
  <section class="hero" role="img" aria-label="Night city street with long-exposure car light trails">
    <header class="site-header">
      <div class="brand">FARELINE</div>
      <nav class="main-nav">
        <a class="active" href="#">HOME</a><a href="#">SHOP</a><a href="#">SERVICES</a><a href="#">INSTALLERS</a><a href="#">CONTACT US</a><a href="#">JOIN US</a>
      </nav>
      <div class="phone">
        <svg width="14" height="14" viewBox="0 0 24 24" fill="none" stroke="#fff" stroke-width="1.6"><path d="M5 3h4l2 5-3 2a12 12 0 0 0 6 6l2-3 5 2v4a2 2 0 0 1-2 2A18 18 0 0 1 3 5a2 2 0 0 1 2-2z"/></svg>
        <span class="phone-number">555.014.2290</span>
        <span class="lang">ENG v</span>
      </div>
      <div class="search">search
        <svg width="10" height="10" viewBox="0 0 12 12" fill="none" stroke="#ccc" stroke-width="1.2"><circle cx="7" cy="5" r="4"/><path d="M4 8l-3 3"/></svg>
      </div>
    </header>
    <h1 class="hero-title">Radio Networks</h1>
    <p class="hero-tagline">CRYSTAL CLEAR MUMMIFICATION.</p>
  </section>

  <main>
    <h2 class="intro-title">Understanding is key.</h2>
    <div class="intro-rule"></div>

    <article class="topic topic-uhf">
      <h2>UHF REPEATER</h2>
      <p>Lorem ipsum dolor sit amet, consectetuer adipiscing elit. Aenean commodo ligula eget dolor. Aenean massa. Cum sociis natoque penatibus et magnis dis parturient montes, nascetur ridiculus mus. Donec qu Lorem ipsum dolor sit amet, consectetuer adipiscing elit. Aenean commodo ligula eget dolor. Aenean massa. Cum sociis natoque penatibus et magnis dis parturient montes, nascetur ridiculus mus. Donec qu</p>
      <p>Lorem ipsum dolor sit amet, consectetuer adipiscing elit. Aenean commodo ligula eget dolor. Aenean massa. Cum sociis natoque penatibus et magnis dis parturient montes, nascetur ridiculus mus. Donec qu</p>
    </article>

    <article class="topic topic-capability">
      <h2>CAPABILITY</h2>
      <p>Lorem ipsum dolor sit amet, consectetuer adipiscing elit. Aenean commodo ligula eget dolor. Aenean massa. Cum sociis natoque penatibus et magnis dis parturient montes, nascetur ridiculus mus. Donec qu Lorem ipsum dolor sit amet, consectetuer adipiscing elit. Aenean commodo ligula eget dolor. Aenean massa. Cum sociis natoque penatibus et magnis dis parturient montes, nascetur ridiculus mus. Donec qu</p>
      <p>Lorem ipsum dolor sit amet, consectetuer adipiscing elit. Aenean commodo ligula eget dolor. Aenean massa. Cum sociis natoque penatibus et magnis dis parturient montes, nascetur ridiculus mus. Donec qu</p>
    </article>

    <article class="topic topic-coverage">
      <h2>COVERAGE</h2>
      <p>Lorem ipsum dolor sit amet, consectetuer adipiscing elit. Aenean commodo ligula eget dolor. Aenean massa. Cum sociis natoque penatibus et magnis dis parturient montes, nascetur ridiculus mus. Donec qu Lorem ipsum dolor sit amet, consectetuer adipiscing elit. Aenean commodo ligula eget dolor. Aenean massa. Cum sociis natoque penatibus et magnis dis parturient montes, nascetur ridiculus mus. Donec qu</p>
      <p>Lorem ipsum dolor sit amet, consectetuer adipiscing elit. Aenean commodo ligula eget dolor. Aenean massa. Cum sociis natoque penatibus et magnis dis parturient montes, nascetur ridiculus mus. Donec qu</p>
    </article>
  </main>

  <footer class="site-footer">
    <div class="footer-col col-about">
      <h3>ABOUT <span>FARELINE</span></h3>
      <p>We provide quality dispatch and meter equipment for indecent taxi &amp; fleet vendors.</p>
    </div>
    <div class="footer-col col-contact">
      <h3>CONTACT INFO</h3>
      <p>Shop Office: (555) 014-2291<br>Customer service: (555) 014-2292<br>Email: <a href="#">hello@fareline.example</a></p>
    </div>
    <div class="footer-col col-hours">
      <h3>HOURS OF SERVICE</h3>
      <p>Monday - Friday: 09:00AM - 09:00PM<br>Saturday: 09:00AM - 07:00PM<br>Sunday: Closed</p>
    </div>
    <div class="footer-col col-links">
      <h3>LINK <span>US</span></h3>
      <div class="social"><span></span><span></span><span></span><span></span><span></span></div>
    </div>
    <div class="footer-rule"></div>
    <p class="legal">© 2018 <a href="#">Fareline.example</a><span class="sep">| Trademarks and brands are the property of their respective owners.</span></p>
  </footer>
</body>
</html>
```